Corvel Capital LLC

Need Professional Business cards for New Investment Fund

Target Market(s)

High Quality investors

Industry/Entity Type

Financial

Contact Information for Business Card

Phone Number +1 555 284 6190
Name Lukas Varenko
Title Fund Manager
email lv@FundCorvel.com
Website www.FundCorvel.com

Colors

Designer to choose colors to be used in the design.

Requirements
Must have
• Must have our Logo and all of the above. Must be made so lettering and loge can be raised

```html
<!DOCTYPE html>
<html lang="en">
<head>
<meta charset="utf-8">
<title>Aldervane – Business Card</title>
<link href="https://fonts.googleapis.com/css2?family=Roboto:wght@400;700&display=swap" rel="stylesheet">
<style>
  :root {
    --backdrop: #3a3a3a;
    --card-dark: #2a2a2a;
    --panel-slate: #414b43;
    --accent-lime: #8cc63e;
    --text-white: #ffffff;
    --mark-grey: #9a9a9a;
  }
  * { margin: 0; padding: 0; box-sizing: border-box; }
  html, body {
    width: 799px;
    height: 1200px;
    overflow: hidden;
    background: var(--backdrop);
    font-family: "Roboto", Arial, sans-serif;
  }
  .card {
    position: absolute;
    left: 90px;
    width: 620px;
    height: 354px;
    overflow: hidden;
    box-shadow: 0 12px 30px rgba(0,0,0,0.45);
  }
  .card-front { top: 130px; background: var(--card-dark); }
  .card-back  { top: 720px; background: var(--panel-slate); }

  .front-brand {
    position: absolute;
    inset: 0;
    display: flex;
    align-items: center;
    justify-content: center;
    gap: 14px;
  }
  .brand-square {
    width: 20px;
    height: 20px;
    background: var(--mark-grey);
  }
  .front-brand .brand-name {
    font-weight: 700;
    font-size: 42px;
    letter-spacing: 3px;
    color: var(--mark-grey);
  }

  .back-shapes { position: absolute; inset: 0; }

  .holder-name {
    position: absolute;
    left: 30px;
    top: 32px;
    font-weight: 700;
    font-size: 27px;
    color: var(--accent-lime);
  }
  .holder-title {
    position: absolute;
    left: 30px;
    top: 66px;
    font-size: 15px;
    font-weight: 400;
    color: var(--text-white);
  }
  .contact-list {
    position: absolute;
    left: 30px;
    top: 238px;
    list-style: none;
  }
  .contact-list li {
    display: flex;
    align-items: center;
    gap: 14px;
    height: 26px;
    font-size: 16px;
    color: var(--text-white);
  }
  .contact-list svg { width: 15px; height: 15px; flex: none; }

  .back-brand {
    position: absolute;
    left: 372px;
    top: 160px;
    display: flex;
    align-items: center;
    gap: 10px;
  }
  .back-brand .brand-square { background: var(--accent-lime); width: 16px; height: 16px; }
  .back-brand .brand-name {
    font-weight: 700;
    font-size: 28px;
    letter-spacing: 2px;
    color: var(--text-white);
  }
</style>
</head>
<body>

<section class="card card-front">
  <div class="front-brand">
    <span class="brand-square"></span>
    <span class="brand-name">ALDERVANE</span>
  </div>
</section>

<section class="card card-back">
  <svg class="back-shapes" viewBox="0 0 620 354" width="620" height="354">
    <path d="M405 0 Q250 150 272 354 L620 354 L620 0 Z" fill="var(--card-dark)"/>
    <path d="M392 0 Q237 150 259 354" fill="none" stroke="var(--accent-lime)" stroke-width="5"/>
  </svg>

  <h1 class="holder-name">Lukas Varenko</h1>
  <p class="holder-title">Fund Manager</p>

  <ul class="contact-list">
    <li>
      <svg viewBox="0 0 16 16"><path fill="var(--accent-lime)" d="M3 1h3l1.5 4-2 1.2a8 8 0 0 0 4.3 4.3L11 8.5l4 1.5v3a2 2 0 0 1-2 2A12 12 0 0 1 1 3a2 2 0 0 1 2-2z"/></svg>
      +1 555 284 6190
    </li>
    <li>
      <svg viewBox="0 0 16 16"><rect x="1" y="3" width="14" height="10" fill="var(--accent-lime)"/><path d="M1 3l7 6 7-6" fill="none" stroke="var(--panel-slate)" stroke-width="1.3"/></svg>
      lv@FundCorvel.com
    </li>
    <li>
      <svg viewBox="0 0 16 16"><circle cx="8" cy="8" r="7" fill="var(--accent-lime)"/><path d="M1 8h14M8 1c-3 3-3 11 0 14M8 1c3 3 3 11 0 14" fill="none" stroke="var(--panel-slate)" stroke-width="1"/></svg>
      www.FundCorvel.com
    </li>
  </ul>

  <div class="back-brand">
    <span class="brand-square"></span>
    <span class="brand-name">ALDERVANE</span>
  </div>
</section>

</body>
</html>
```